WordPress webdesign with coding for our company BRISK The Answer

BRISK The Answer is a payrolling company such as Montaval Wages (one of our competitor https://www.montaval-wages.ch/fr/). We need to set up our website in both languages (Fr and Eng). Our logo is enclosed.
we would like something simple explaining what is payrolling in Graph and wording, who we are and a contact page. you can also take some example if needed from our mother company BRISK The Horizon (www.briskthehorizon.ch) or our sister company (www.briskyourstride.ch). we would like to keep the color panel of our logo (ref. Black = PANTONE P Process Black C
Pink = PANTONE P Process Magenta C
Grey = PANTONE 430 C) as the driver of the website.

```html
<!DOCTYPE html>
<html lang="en">
<head>
<meta charset="utf-8">
<title>BRISK The Answer – Payrolling</title>
<link rel="stylesheet" href="https://fonts.googleapis.com/css2?family=Figtree:wght@400;500;600;700;800&display=swap">
<style>
  :root {
    --pink: #e8318f;
    --ink: #1a1a1a;
    --text: #2b2b2b;
    --grey: #7c7f8c;
    --light: #f4f4f4;
    --line: #d9d9d9;
    --white: #ffffff;
  }
  * { margin: 0; padding: 0; box-sizing: border-box; }
  html, body { width: 1200px; height: 3118px; overflow: hidden; }
  body { position: relative; background: var(--white); font-family: "Figtree", sans-serif; color: var(--text); }
  .abs { position: absolute; }
  .accent { color: var(--pink); }
  .btn {
    position: absolute; display: flex; align-items: center; justify-content: center;
    background: var(--pink); color: var(--white); font-weight: 700; font-size: 16px;
    border-radius: 0 14px 0 14px; text-transform: uppercase; letter-spacing: .2px;
  }
  .section-title { position: absolute; font-weight: 700; color: var(--ink); font-size: 44px; line-height: 1; }
  .body-copy { position: absolute; font-size: 13.5px; line-height: 19.3px; color: var(--ink); }
  .body-copy p + p { margin-top: 19px; }

  /* Header */
  .site-header { position: absolute; left: 0; top: 0; width: 1200px; height: 99px; background: var(--white); border-bottom: 1px solid var(--line); }
  .brand { position: absolute; left: 138px; top: 26px; font-size: 40px; font-weight: 800; color: var(--ink); letter-spacing: 1px; line-height: 1; }
  .brand-sub { position: absolute; left: 138px; top: 70px; font-size: 12px; font-weight: 500; color: var(--ink); letter-spacing: 9px; }
  .main-nav { position: absolute; top: 43px; display: flex; gap: 0; font-size: 15.5px; color: var(--ink); }
  .main-nav span { position: absolute; white-space: nowrap; }
  .lang-switch { position: absolute; left: 980px; top: 29px; width: 83px; height: 47px; background: var(--pink); color: var(--white); border-radius: 0 12px 0 12px; font-weight: 700; font-size: 15px; display: flex; align-items: center; padding-left: 17px; gap: 16px; }

  /* Hero */
  .hero { position: absolute; left: 0; top: 99px; width: 1200px; height: 615px; overflow: hidden; }
  .hero-photo { position: absolute; inset: 0; background: linear-gradient(100deg, #efeeec 0%, #e9e7e4 40%, #d9d4cf 62%, #c9c3bd 80%, #dcd9d6 100%); }
  .hero-title { position: absolute; left: 138px; top: 196px; font-size: 46px; font-weight: 700; color: var(--ink); line-height: 1; }
  .hero-text { position: absolute; left: 138px; top: 255px; width: 480px; font-size: 19px; line-height: 23px; color: var(--ink); }
  .hero-dots { position: absolute; left: 147px; top: 451px; display: flex; gap: 7px; }
  .hero-dots i { width: 10px; height: 10px; border-radius: 50%; background: var(--pink); display: block; }
  .hero-dots i.open { background: transparent; border: 1.5px solid var(--pink); }

  /* Payrolling */
  .chart-card { position: absolute; left: 138px; top: 754px; width: 452px; height: 398px; background: var(--light); border-radius: 18px; }

  /* Services */
  .services { position: absolute; left: 0; top: 1236px; width: 1200px; height: 483px; background: var(--light); }
  .service-card { position: absolute; top: 195px; width: 294px; height: 189px; border: 1.5px solid var(--pink); border-radius: 0 24px 0 24px; text-align: center; }
  .service-icon { position: absolute; left: 103px; top: -44px; width: 88px; height: 88px; border-radius: 50%; background: var(--white); border: 1.5px solid var(--pink); }
  .service-name { position: absolute; left: 0; right: 0; top: 54px; font-size: 23px; font-weight: 700; color: var(--pink); }
  .service-text { position: absolute; left: 30px; right: 30px; top: 96px; font-size: 13.5px; line-height: 19.5px; color: var(--ink); }
  .service-plus { position: absolute; left: 128px; bottom: -19px; width: 37px; height: 37px; border-radius: 50%; background: var(--light); border: 1.5px solid var(--pink); color: var(--pink); font-size: 20px; line-height: 32px; }

  /* Contact */
  .contact { position: absolute; left: 0; top: 2203px; width: 1200px; height: 637px; overflow: hidden; }
  .contact-photo { position: absolute; inset: 0; background: linear-gradient(90deg, #c7c9c0 0%, #8a8f84 20%, #3a3b3a 35%, #4a4c48 50%, #a9ad9f 70%, #d5d7cf 100%); }
  .contact-card { position: absolute; left: 608px; top: 53px; width: 454px; height: 542px; background: var(--white); border-radius: 18px; }
  .field { position: absolute; left: 33px; width: 387px; font-size: 15px; color: var(--ink); padding-left: 3px; border-bottom: 1.5px solid var(--pink); padding-bottom: 10px; }
  .field.neutral { border-bottom-color: var(--grey); }

  /* Footer */
  .site-footer { position: absolute; left: 0; top: 2840px; width: 1200px; height: 278px; background: var(--grey); color: var(--white); text-align: center; }
  .footer-brand { position: absolute; left: 0; right: 0; top: 50px; font-size: 40px; font-weight: 800; letter-spacing: 1px; line-height: 1; }
  .footer-sub { position: absolute; left: 0; right: 0; top: 94px; font-size: 12px; letter-spacing: 9px; }
  .footer-nav span { position: absolute; top: 125px; font-size: 15.5px; white-space: nowrap; }
  .socials { position: absolute; left: 543px; top: 166px; display: flex; gap: 11px; }
  .socials i { display: block; width: 30px; height: 30px; border-radius: 50%; background: var(--ink); }
  .socials i.active { background: var(--pink); }
  .copyright { position: absolute; left: 0; right: 0; top: 218px; font-size: 15px; }
</style>
</head>
<body>

<header class="site-header">
  <div class="brand">BRISK</div>
  <div class="brand-sub">THE ANSWER</div>
  <nav class="main-nav">
    <span class="accent" style="left:486px;font-weight:600">Home</span>
    <span style="left:567px">What is payrolling</span>
    <span style="left:728px">Who we are</span>
    <span style="left:853px">Contact</span>
  </nav>
  <div class="lang-switch">EN
    <svg width="12" height="8" viewBox="0 0 12 8"><path d="M1 1l5 5 5-5" fill="none" stroke="#fff" stroke-width="2"/></svg>
  </div>
</header>

<section class="hero">
  <div class="hero-photo" role="img" aria-label="Smiling businesswoman holding a coffee cup while working at a laptop in a bright office"></div>
  <svg class="abs" style="left:0;top:0" width="1200" height="615" viewBox="0 0 1200 615">
    <polygon points="0,593 1200,542 1200,615 0,615" fill="#fff"/>
    <polygon points="472,564 1200,518 1200,615" fill="var(--pink)"/>
  </svg>
  <h1 class="hero-title">BRISK <span class="accent">The Answer</span></h1>
  <p class="hero-text">Lorem ipsum dolor sit amet, consectetur adipiscing elit, sed do eiusmod tempor incididunt ut labore et dolore magna aliqua.</p>
  <a class="btn" style="left:138px;top:358px;width:213px;height:46px">Discover payrolling</a>
  <div class="hero-dots"><i></i><i></i><i class="open"></i><i></i></div>
</section>

<section class="payrolling">
  <div class="chart-card">
    <svg width="452" height="398" viewBox="0 0 452 398" font-family="Figtree, sans-serif">
      <text x="222" y="38" font-size="17" font-weight="500" fill="#6b6b6b" text-anchor="middle">Payroll</text>
      <g font-size="13.5" fill="#6b6b6b" text-anchor="end">
        <text x="41" y="53">60.k</text>
        <text x="41" y="108">50.k</text>
        <text x="41" y="157">40.k</text>
        <text x="41" y="207">30.k</text>
        <text x="41" y="257">20.k</text>
        <text x="41" y="315">10.k</text>
      </g>
      <line x1="46" y1="34" x2="46" y2="362" stroke="var(--pink)" stroke-width="1"/>
      <line x1="24" y1="336" x2="436" y2="336" stroke="var(--pink)" stroke-width="1"/>
      <g font-size="13.5" fill="#6b6b6b" text-anchor="middle">
        <text x="80" y="356">Mon</text><text x="140" y="356">Tue</text><text x="206" y="356">Wed</text>
        <text x="272" y="356">Thu</text><text x="333" y="356">Fri</text><text x="392" y="356">Sat</text>
      </g>
      <path d="M56,319 C66,292 76,270 89,256 C120,222 160,220 194,213 C250,198 275,110 322,105 C350,102 365,130 385,125 C405,120 418,100 425,89" fill="none" stroke="var(--pink)" stroke-width="1.5"/>
      <g fill="var(--pink)"><circle cx="56" cy="319" r="3"/><circle cx="89" cy="256" r="3"/><circle cx="194" cy="213" r="3"/><circle cx="322" cy="105" r="3"/></g>
      <g font-size="12" fill="#6b6b6b">
        <text x="95" y="271">Lorem Ipsum</text>
        <text x="155" y="195">Lorem Ipsum</text>
        <text x="284" y="93">Lorem Ipsum</text>
      </g>
    </svg>
  </div>
  <h2 class="section-title" style="left:613px;top:786px">What is <span class="accent">Payrolling</span></h2>
  <div class="body-copy" style="left:613px;top:862px;width:450px">
    <p>Lorem ipsum dolor sit amet, consectetur adipiscing elit, sed do eiusmod tempor incididunt ut labore et dolore magna aliqua. Quis ipsum suspendisse ultrices gravida. Risus commodo viverra maecenas accumsan lacus vel facilisis.</p>
    <p>Lorem ipsum dolor sit amet, consectetur adipiscing elit, sed do eiusmod tempor incididunt ut labore et dolore magna aliqua. Quis ipsum suspendisse ultrices gravida. Risus commodo viverra maecenas accumsan lacus vel facilisis.</p>
  </div>
  <a class="btn" style="left:613px;top:1057px;width:135px;height:47px">Learn more</a>
</section>

<section class="services">
  <h2 class="section-title" style="left:0;right:0;top:52px;text-align:center">Discover all <span class="accent">Our Services</span></h2>
  <div class="service-card" style="left:138px">
    <div class="service-icon">
      <svg width="88" height="88" viewBox="0 0 88 88" fill="none" stroke="var(--ink)" stroke-width="2"><circle cx="36" cy="34" r="8"/><path d="M22 62c0-10 6-16 14-16s14 6 14 16"/><rect x="46" y="22" width="14" height="18"/><circle cx="56" cy="54" r="8" stroke="var(--pink)"/></svg>
    </div>
    <div class="service-name">Payrolling</div>
    <div class="service-text">Lorem ipsum dolor sit amet, consectetur adipiscing elit, sed do eiusmod tempor incididunt</div>
    <div class="service-plus">+</div>
  </div>
  <div class="service-card" style="left:454px">
    <div class="service-icon">
      <svg width="88" height="88" viewBox="0 0 88 88" fill="none" stroke="var(--ink)" stroke-width="2"><rect x="28" y="24" width="30" height="40"/><path d="M34 32h18M34 38h18M34 44h12"/><rect x="32" y="52" width="22" height="8" stroke="var(--pink)"/></svg>
    </div>
    <div class="service-name">Sourcing</div>
    <div class="service-text">Lorem ipsum dolor sit amet, consectetur adipiscing elit, sed do eiusmod tempor incididunt</div>
    <div class="service-plus">+</div>
  </div>
  <div class="service-card" style="left:769px">
    <div class="service-icon">
      <svg width="88" height="88" viewBox="0 0 88 88" fill="none" stroke="var(--ink)" stroke-width="2"><circle cx="44" cy="44" r="8" stroke="var(--pink)"/><path d="M44 36V20M44 52v16M36 44H20M52 44h16M38 38l-10-10M50 50l10 10M50 38l10-10M38 50l-10 10"/></svg>
    </div>
    <div class="service-name">Payroll Outsourcing</div>
    <div class="service-text">Lorem ipsum dolor sit amet, consectetur adipiscing elit, sed do eiusmod tempor incididunt</div>
    <div class="service-plus">+</div>
  </div>
</section>

<section class="who-we-are">
  <h2 class="section-title" style="left:138px;top:1794px">Who <span class="accent">We Are</span></h2>
  <div class="body-copy" style="left:138px;top:1858px;width:450px">
    <p>Lorem ipsum dolor sit amet, consectetur adipiscing elit, sed do eiusmod tempor incididunt ut labore et dolore magna aliqua. Quis ipsum suspendisse ultrices gravida. Risus commodo viverra maecenas accumsan lacus vel facilisis.</p>
    <p>Lorem ipsum dolor sit amet, consectetur adipiscing elit, sed do eiusmod tempor incididunt ut labore et dolore magna aliqua. Quis ipsum suspendisse ultrices gravida. Risus commodo viverra maecenas accumsan lacus vel facilisis.</p>
  </div>
  <a class="btn" style="left:138px;top:2054px;width:140px;height:47px">Learn more</a>
  <svg class="abs" style="left:630px;top:1748px" width="420" height="420" viewBox="0 0 420 420">
    <path d="M226 4 C120 -4 16 70 8 190 C4 270 40 330 100 370 C50 320 28 260 36 190 C48 90 130 14 226 4 Z" fill="var(--pink)"/>
  </svg>
  <div class="abs" role="img" aria-label="Businesswoman laughing on a phone call in a sunlit office" style="left:654px;top:1764px;width:392px;height:390px;border-radius:50%;background:radial-gradient(circle at 70% 40%, #f3f0ea 0%, #cfcac2 45%, #8c8780 75%, #5c5853 100%)"></div>
</section>

<section class="contact">
  <div class="contact-photo" role="img" aria-label="Smiling woman typing on a laptop at a desk with plants in the background"></div>
  <div class="contact-card">
    <h2 class="section-title" style="left:36px;top:49px">Contact <span class="accent">Us</span></h2>
    <div class="field" style="top:134px">Name</div>
    <div class="field neutral" style="top:199px">Email</div>
    <div class="field neutral" style="top:265px">Phone</div>
    <div class="field" style="top:370px">Message</div>
    <a class="btn" style="left:158px;top:445px;width:139px;height:47px">Submit</a>
  </div>
</section>

<footer class="site-footer">
  <div class="footer-brand">BRISK</div>
  <div class="footer-sub">THE ANSWER</div>
  <nav class="footer-nav">
    <span style="left:389px;font-weight:700">Home</span>
    <span style="left:470px">What is payrolling</span>
    <span style="left:631px">Who we are</span>
    <span style="left:756px">Contact</span>
  </nav>
  <div class="socials"><i></i><i class="active"></i><i></i></div>
  <div class="copyright">© 2025 | www.brisktheanswer.com</div>
</footer>

</body>
</html>
```